Prayer Grotto - NO FURTHER SUBMISSIONS NEEDED THANKS

We are launching an online Christian prayer grotto to promote unity and peace for Christians and with friends of other faiths. A main feature of the website is our virtual grotto where people can light candles for intentions.
We've hit a snag in the design because no art we can find and try looks good in the banner. It is not a logo. And we have website designers already doing work that is good. We just need the illustration for the banner.
IMAGINE: An ancient grotto tucked into the woods, a peaceful place where people must walk far from the busy world.
ATTACHED "IMAGES SUGGESTED" can help for detail but here is description.
The SIGN is barn wood, old wood, very weathered, and gray tones mostly. It can have paint sloshed on it. I'd like nails and a lot of grain to show, very weathered and many shades of gray, from very light almost white to charcoal. The site has all those colors.
HUES for the grays? See the attached for the red/yellow candles of the final site. We are using jewel colors of gold, bronze, red and for print DARK CHARCOAL GRAY.
The main words are Linden Murmurs. Font should be vintage too. Goudy Old Style is a good one, but use your judgment. Font must be WITH SERIF.
To the left of "Linden Murmurs" on the sign is a SMALL discreet Cross burned into the wood too ... it has two layers, a back layer that is dark etched into the wood. It has a forward layer that might be metal, bronze. Ideally it would be two nails forming a cross. The nails would look like the big nails used in railroad ties.
To the right of the "Linden Murmurs" on the sign is an almost hard to see etching of a rose, or just a shadow of a rose.
The art needs to communicate place, grotto, old, peace, quite, ancient, weathered and gentle.
Attached are:
TWO images of the Linden Murmurs sign on the website in place with comments. You'll see how the Cross works.
ONE image of the rose.
IGNORE ANY COMMENTS In these images about STONE behind the sign. I changed my mind. I just need a sign like you see to put in place.

```html
<!DOCTYPE html>
<html lang="en">
<head>
<meta charset="utf-8">
<title>Linden Murmurs – Sign Wrap</title>
<link rel="stylesheet" href="https://fonts.googleapis.com/css2?family=Sorts+Mill+Goudy&display=swap">
<style>
  :root {
    --page: #ffffff;
    --wood-dark: #4f4f52;
    --wood-mid: #6c6b6d;
    --wood-light: #8a8889;
    --grain: rgba(40, 40, 42, 0.18);
    --ink: #353436;
    --etch: #2e2d2f;
    --bronze: #8f6b3e;
    --bronze-light: #b88c55;
    --rose-core: #5a5a5c;
    --rose-edge: rgba(90, 90, 92, 0);
  }
  * { margin: 0; padding: 0; box-sizing: border-box; }
  html, body {
    width: 1200px;
    height: 900px;
    overflow: hidden;
    background: var(--page);
  }
  .canvas {
    position: relative;
    width: 1200px;
    height: 900px;
    background: var(--page);
  }
  .panel { position: absolute; }
  .panel--top,
  .panel--bottom {
    left: 437px;
    width: 309px;
    background:
      repeating-linear-gradient(90deg, transparent 0 9px, var(--grain) 9px 10px, transparent 10px 23px),
      linear-gradient(90deg, var(--wood-dark) 0%, var(--wood-mid) 45%, var(--wood-dark) 70%, var(--wood-mid) 100%);
  }
  .panel--top { top: 33px; height: 242px; }
  .panel--bottom { top: 604px; height: 263px; }
  .panel--face {
    left: 67px;
    top: 285px;
    width: 1052px;
    height: 308px;
    overflow: hidden;
  }
  .face-wood {
    position: absolute;
    inset: 0;
    background:
      repeating-linear-gradient(180deg, transparent 0 7px, var(--grain) 7px 8px, transparent 8px 19px),
      linear-gradient(180deg, var(--wood-mid) 0%, var(--wood-light) 45%, var(--wood-mid) 75%, var(--wood-dark) 100%);
  }
  .nail-cross {
    position: absolute;
    left: 14px;
    top: 104px;
    width: 50px;
    height: 78px;
  }
  .sign-name {
    position: absolute;
    left: 76px;
    top: 110px;
    font-family: "Sorts Mill Goudy", "Goudy Old Style", serif;
    font-weight: 400;
    font-size: 80px;
    line-height: 1;
    letter-spacing: 1px;
    color: var(--ink);
    white-space: nowrap;
  }
  .rose-etching {
    position: absolute;
    left: 660px;
    top: 3px;
    width: 392px;
    height: 300px;
    background:
      radial-gradient(ellipse 140px 140px at 238px 150px, var(--rose-core) 0%, var(--rose-core) 70%, var(--rose-edge) 100%),
      linear-gradient(160deg, var(--rose-edge) 0%, var(--rose-edge) 30%, rgba(110,110,112,0.5) 55%, var(--rose-edge) 75%);
  }
</style>
</head>
<body>
  <main class="canvas">
    <div class="panel panel--top" role="img" aria-label="Weathered gray barn wood with vertical grain"></div>

    <section class="panel panel--face">
      <div class="face-wood" role="img" aria-label="Weathered gray barn wood sign with horizontal grain"></div>
      <svg class="nail-cross" viewBox="0 0 50 78" aria-hidden="true">
        <g class="nail-cross__etch" fill="var(--etch)" opacity="0.55">
          <rect x="21" y="2" width="10" height="76" rx="2"/>
          <rect x="2" y="20" width="48" height="10" rx="2"/>
        </g>
        <g class="nail-cross__nails">
          <rect x="19" y="0" width="8" height="72" rx="1.5" fill="var(--bronze)"/>
          <rect x="16" y="0" width="14" height="5" rx="1" fill="var(--bronze-light)"/>
          <rect x="0" y="18" width="44" height="8" rx="1.5" fill="var(--bronze)"/>
          <rect x="0" y="15" width="5" height="14" rx="1" fill="var(--bronze-light)"/>
        </g>
      </svg>
      <h1 class="sign-name">Linden Murmurs</h1>
      <div class="rose-etching" role="img" aria-label="Gray etched rose with stem and leaves"></div>
    </section>

    <div class="panel panel--bottom" role="img" aria-label="Weathered gray barn wood with vertical grain"></div>
  </main>
</body>
</html>
```